Business Card Design For Marketing Agnecy LVP

Need business card design for marketing agency.

Doug Fenwick
President, CEO
1-555-302-4196
doug@boldpromoperksgroup.example
www.BoldPromoPerksGroup.example

Back Side:
Boost Sales Using Rewards, Incentives & Giveaways
Get A Free Sample Package

Target Market(s)

B2B

Industry/Entity Type

Marketing

Contact Information for Business Card

Doug Fenwick
President, CEO
1-555-302-4196

Back Side:
Get A Free Sample Package

Please note that my current url is OLD DESIGN. I am working on new design and want the business card to match color themes at least on new site. Here is the demo link for new site so you can see the colors I use, etc.

http://layoutcratehub.example/kq/doug/lvp_final/index.html

Requirements
Must have
• Please note that my current url is OLD DESIGN. I am working on new design and want the business card to match color themes at least on new site. Here is the demo link for new site so you can see the colors I use, etc.

Nice to have

Should not have

```html
<!DOCTYPE html>
<html lang="en">
<head>
<meta charset="UTF-8">
<title>LVP Business Card</title>
<link rel="stylesheet" href="https://fonts.googleapis.com/css2?family=Roboto:wght@400;500&family=Montserrat:wght@700&display=swap">
<style>
  :root {
    --backdrop: #3b3b3d;
    --card: #1d1e20;
    --card-edge: #141516;
    --gloss: #4e4f52;
    --brand-blue: #3a70bf;
    --text-light: #f2f2f2;
  }
  * { margin: 0; padding: 0; box-sizing: border-box; }
  html, body {
    width: 799px;
    height: 1200px;
    overflow: hidden;
    background: var(--backdrop);
    font-family: "Roboto", sans-serif;
  }
  .sheet {
    position: relative;
    width: 799px;
    height: 1200px;
    display: flex;
    flex-direction: column;
    align-items: center;
    justify-content: space-around;
    padding: 60px 0;
  }
  .card {
    position: relative;
    width: 620px;
    height: 354px;
    background: var(--card);
    border: 1px solid var(--card-edge);
    box-shadow: 0 14px 30px rgba(0,0,0,0.45);
  }
  .card-front {
    display: flex;
    align-items: center;
    justify-content: center;
  }
  .brand-mark {
    display: flex;
    align-items: center;
    gap: 14px;
    font-family: "Montserrat", sans-serif;
    font-weight: 700;
  }
  .brand-mark .dot {
    border-radius: 50%;
    flex: none;
  }
  .card-front .brand-mark {
    color: var(--gloss);
    font-size: 34px;
    line-height: 1.15;
    text-transform: uppercase;
    letter-spacing: 1px;
  }
  .card-front .brand-mark .dot {
    width: 26px;
    height: 26px;
    background: var(--gloss);
  }
  .card-back {
    display: flex;
    align-items: center;
    padding: 0 40px 0 36px;
    gap: 34px;
  }
  .card-back .brand-mark {
    color: var(--brand-blue);
    font-size: 24px;
    line-height: 1.15;
    text-transform: uppercase;
    width: 230px;
  }
  .card-back .brand-mark .dot {
    width: 16px;
    height: 16px;
    background: var(--brand-blue);
  }
  .contact-block { color: var(--text-light); }
  .contact-name {
    color: var(--brand-blue);
    font-size: 21px;
    font-weight: 500;
    letter-spacing: 0.5px;
  }
  .contact-title {
    font-size: 15px;
    margin: 2px 0 22px;
  }
  .contact-list { list-style: none; }
  .contact-list li {
    display: flex;
    align-items: center;
    gap: 9px;
    font-size: 14.5px;
    margin-bottom: 5px;
  }
  .contact-list svg {
    width: 13px;
    height: 13px;
    flex: none;
    fill: var(--brand-blue);
  }
</style>
</head>
<body>
<main class="sheet">
  <section class="card card-front" aria-label="Card front">
    <div class="brand-mark">
      <span class="dot"></span>
      <span class="brand-name">LVP Bold Promo<br>Perks Group</span>
    </div>
  </section>

  <section class="card card-back" aria-label="Card back">
    <div class="brand-mark">
      <span class="dot"></span>
      <span class="brand-name">LVP Bold Promo Perks Group</span>
    </div>
    <div class="contact-block">
      <p class="contact-name">Doug Fenwick</p>
      <p class="contact-title">President, CEO</p>
      <ul class="contact-list">
        <li>
          <svg viewBox="0 0 24 24" aria-hidden="true"><path d="M6.6 10.8a15.1 15.1 0 0 0 6.6 6.6l2.2-2.2a1 1 0 0 1 1-.25 11.4 11.4 0 0 0 3.6.57 1 1 0 0 1 1 1V20a1 1 0 0 1-1 1A17 17 0 0 1 3 4a1 1 0 0 1 1-1h3.5a1 1 0 0 1 1 1c0 1.25.2 2.45.57 3.57a1 1 0 0 1-.25 1z"/></svg>
          <span>1-555-302-4196</span>
        </li>
        <li>
          <svg viewBox="0 0 24 24" aria-hidden="true"><path d="M2 5h20v14H2zm2 2v.5l8 5 8-5V7l-8 5z"/></svg>
          <span>doug@boldpromoperksgroup.example</span>
        </li>
        <li>
          <svg viewBox="0 0 24 24" aria-hidden="true"><path d="M12 2a10 10 0 1 0 0 20 10 10 0 0 0 0-20zm0 2c.9 0 2.2 2 2.6 5H9.4C9.8 6 11.1 4 12 4zM4.3 13a8 8 0 0 1 0-2h3a17 17 0 0 0 0 2zm.8 2h2.5a11 11 0 0 0 1.3 3.5A8 8 0 0 1 5.1 15zm2.5-6H5.1a8 8 0 0 1 3.8-3.5A11 11 0 0 0 7.6 9zM12 20c-.9 0-2.2-2-2.6-5h5.2c-.4 3-1.7 5-2.6 5zm2.8-7H9.2a15 15 0 0 1 0-2h5.6a15 15 0 0 1 0 2zm.3 5.5a11 11 0 0 0 1.3-3.5h2.5a8 8 0 0 1-3.8 3.5zM16.7 13a17 17 0 0 0 0-2h3a8 8 0 0 1 0 2zm-.3-4a11 11 0 0 0-1.3-3.5A8 8 0 0 1 18.9 9z"/></svg>
          <span>www.BoldPromoPerksGroup.example</span>
        </li>
      </ul>
    </div>
  </section>
</main>
</body>
</html>
```